Business Card Design Project

After recently finishing a design project for the company logo using markbazaar, it's now time for a business card. Attached to this is the logo.

The requirements for the business card are pretty straightforward:

- A clean, uncomplicated look
- Consistent usage of fonts
- Designs for both single sided and double sided cards
- A modern layout with preferably space to refer to social media accounts and/or downloadable vcards through a qr code
- consistent application of the company colour scheme: red/white. Hex codes for exact colour can be provided

Thanks!

```html
<!DOCTYPE html>
<html lang="en">
<head>
<meta charset="utf-8">
<title>Clayforge Staffing – Business Cards</title>
<link rel="stylesheet" href="https://fonts.googleapis.com/css2?family=Source+Sans+3:ital,wght@0,400;0,600;0,700;1,700&display=swap">
<style>
  :root {
    --backdrop: #b07d52;
    --card: #ffffff;
    --brand-red: #e31e26;
    --band-grey: #898989;
    --ink: #231f20;
    --on-dark: #ffffff;
    --card-shadow: rgba(40, 20, 5, 0.45);
  }
  * { box-sizing: border-box; margin: 0; padding: 0; }
  html, body {
    width: 960px;
    height: 1200px;
    overflow: hidden;
  }
  body {
    position: relative;
    background: var(--backdrop);
    font-family: "Source Sans 3", "Myriad Pro", Arial, sans-serif;
    color: var(--ink);
  }
  .card {
    position: absolute;
    left: 60px;
    width: 840px;
    height: 479px;
    background: var(--card);
    border-radius: 32px;
    overflow: hidden;
    box-shadow: 6px 8px 14px var(--card-shadow);
  }
  .card--front { top: 90px; }
  .card--back { top: 638px; }

  .wordmark {
    position: absolute;
    left: 0;
    right: 0;
    display: flex;
    align-items: center;
    justify-content: center;
    gap: 22px;
  }
  .card--front .wordmark { top: 120px; }
  .card--back .wordmark { top: 200px; }
  .wordmark__square {
    width: 58px;
    height: 58px;
    background: var(--brand-red);
    flex: none;
  }
  .wordmark__name {
    font-size: 66px;
    font-weight: 600;
    letter-spacing: -0.5px;
    color: var(--ink);
    line-height: 1;
  }

  .contact-band {
    position: absolute;
    left: 0;
    top: 304px;
    width: 840px;
    height: 103px;
  }
  .contact-band svg { position: absolute; inset: 0; }
  .band-red { fill: var(--brand-red); }
  .band-grey { fill: var(--band-grey); }

  .holder {
    position: absolute;
    left: 80px;
    top: 24px;
    color: var(--on-dark);
  }
  .holder__name {
    font-size: 26px;
    font-weight: 700;
    line-height: 1.1;
  }
  .holder__role {
    font-size: 20px;
    font-weight: 400;
    margin-top: 4px;
  }

  .contact-list {
    position: absolute;
    right: 70px;
    top: 14px;
    list-style: none;
    text-align: right;
    color: var(--on-dark);
    font-size: 20px;
    line-height: 29px;
  }
  .contact-list__label {
    font-weight: 700;
    font-style: italic;
  }

  .address {
    position: absolute;
    left: 0;
    right: 0;
    top: 430px;
    text-align: center;
    font-size: 25px;
    color: var(--ink);
  }
</style>
</head>
<body>

  <section class="card card--front" aria-label="Business card front">
    <div class="wordmark">
      <span class="wordmark__square" aria-hidden="true"></span>
      <span class="wordmark__name">Clayforge Staffing</span>
    </div>

    <div class="contact-band">
      <svg width="840" height="103" viewBox="0 0 840 103" aria-hidden="true">
        <polygon class="band-red" points="0,0 383,0 288,103 0,103"/>
        <polygon class="band-grey" points="402,0 840,0 840,103 306,103"/>
      </svg>
      <div class="holder">
        <p class="holder__name">Your Name</p>
        <p class="holder__role">Designation</p>
      </div>
      <ul class="contact-list">
        <li><span class="contact-list__label">t</span> : 123-123-1234</li>
        <li><span class="contact-list__label">e</span> : info@yourwebsite.com</li>
        <li><span class="contact-list__label">w</span> : www.clayforge.com</li>
      </ul>
    </div>

    <p class="address">1234, Street Name, District, City, Country Code.</p>
  </section>

  <section class="card card--back" aria-label="Business card back">
    <div class="wordmark">
      <span class="wordmark__square" aria-hidden="true"></span>
      <span class="wordmark__name">Clayforge Staffing</span>
    </div>
  </section>

</body>
</html>
```